Home Remodeling company needs a business card design

we need a business card design for home remodeling company in hamilton county, indiana USA. we offers a wide range of construction services including whole house renovations, Design and Build Basements and Kitchen and Bathroom Remodeling . we would like to see designs for both site of business card that use the same color of the company logo and also including all information below :
1- Karim Feltous CEO / General Contractor
2- all company contacts Telephone numbers ( 1-888-DULOM-47 ) ( 317-555-0193) email address ( info@dulomhome.com) website ( www.dulomhome.com ) and social media logos (Facebook- twitter- google plus )
3- company logo
4- licensed . insured . bonded

```html
<!DOCTYPE html>
<html lang="en">
<head>
<meta charset="utf-8">
<title>Dulom Home Remodeling – Business Card</title>
<link href="https://fonts.googleapis.com/css2?family=Cabin:wght@400;500;600;700&display=swap" rel="stylesheet">
<style>
  :root {
    --backdrop: #8f8f91;
    --card-light: #ececee;
    --card-dark: #39393b;
    --ink: #2f2f31;
    --ink-soft: #4a4a4c;
    --accent-red: #c3202b;
    --logo-light: #dcdcde;
    --rule: #6c6c6e;
  }
  * { margin: 0; padding: 0; box-sizing: border-box; }
  html, body {
    width: 1105px;
    height: 1200px;
    overflow: hidden;
    background: var(--backdrop);
    font-family: "Cabin", sans-serif;
  }
  .card {
    position: absolute;
    left: 180px;
    width: 746px;
    height: 426px;
    overflow: hidden;
  }
  .card-front { top: 118px; background: var(--card-light); }
  .card-back  { top: 638px; background: var(--card-dark); }

  /* Wordmark */
  .wordmark { position: absolute; display: flex; flex-direction: column; }
  .wordmark-row { display: flex; align-items: center; gap: 10px; }
  .wordmark-square { background: var(--accent-red); }
  .wordmark-name { font-weight: 700; line-height: 1; letter-spacing: 1px; }
  .wordmark-tagline { font-weight: 400; letter-spacing: 5px; line-height: 1; }

  .card-front .wordmark { left: 62px; top: 170px; }
  .card-front .wordmark-square { width: 12px; height: 12px; }
  .card-front .wordmark-name { font-size: 46px; color: var(--ink); }
  .card-front .wordmark-tagline { font-size: 15px; color: var(--ink-soft); margin-top: 4px; margin-left: 22px; }

  .card-back .wordmark { left: 0; right: 0; top: 165px; align-items: center; }
  .card-back .wordmark-square { width: 15px; height: 15px; background: var(--logo-light); }
  .card-back .wordmark-name { font-size: 62px; color: var(--logo-light); }
  .card-back .wordmark-tagline { font-size: 19px; letter-spacing: 6.5px; color: var(--logo-light); margin-top: 6px; }

  /* Front details */
  .divider {
    position: absolute; left: 390px; top: 108px;
    width: 1.5px; height: 180px; background: var(--rule);
  }
  .contact-block { position: absolute; left: 432px; top: 102px; color: var(--ink); }
  .person-name { font-size: 27px; font-weight: 600; line-height: 1.2; }
  .person-title { font-size: 20px; color: var(--accent-red); line-height: 1.3; margin-bottom: 12px; }
  .contact-list { list-style: none; }
  .contact-item {
    display: flex; align-items: center; gap: 10px;
    font-size: 19px; line-height: 29px; color: var(--ink);
  }
  .contact-item svg { width: 16px; height: 16px; fill: var(--ink); flex: none; }

  .credential-band { position: absolute; left: 0; bottom: 0; width: 746px; height: 56px; }
  .credentials {
    position: absolute; right: 26px; bottom: 12px;
    font-size: 20px; color: #ffffff; letter-spacing: 0.3px;
  }

  /* Back social row */
  .social-row {
    position: absolute; left: 0; right: 0; top: 358px;
    display: flex; justify-content: center; align-items: center; gap: 6px;
  }
  .social-rule { width: 58px; height: 1px; background: #7a7a7c; }
  .social-dot { width: 28px; height: 28px; border-radius: 50%; background: #e6e6e8; }
</style>
</head>
<body>

<section class="card card-front" aria-label="Business card front">
  <div class="wordmark">
    <div class="wordmark-row">
      <span class="wordmark-square"></span>
      <span class="wordmark-name">DULOM</span>
    </div>
    <span class="wordmark-tagline">HOME REMODELING</span>
  </div>

  <div class="divider"></div>

  <div class="contact-block">
    <p class="person-name">Karim Feltous</p>
    <p class="person-title">CEO / General Contractor</p>
    <ul class="contact-list">
      <li class="contact-item">
        <svg viewBox="0 0 16 16"><path d="M3.6 1.2l2.3 2.6-1.3 2a9 9 0 0 0 5.6 5.6l2-1.3 2.6 2.3-1.3 2.4C7 14.5 1.5 9 1.2 2.5z"/></svg>
        1-888-DULOM-47
      </li>
      <li class="contact-item">
        <svg viewBox="0 0 16 16"><path d="M4 0h8a1 1 0 0 1 1 1v14a1 1 0 0 1-1 1H4a1 1 0 0 1-1-1V1a1 1 0 0 1 1-1zm.8 2v10.5h6.4V2zM8 13.3a.9.9 0 1 0 0 1.8.9.9 0 0 0 0-1.8z"/></svg>
        317-555-0193
      </li>
      <li class="contact-item">
        <svg viewBox="0 0 16 16"><path d="M1 3h14v10H1zm1.4 1.3L8 8.6l5.6-4.3z"/></svg>
        info@dulomhome.com
      </li>
      <li class="contact-item">
        <svg viewBox="0 0 16 16"><path d="M8 .5a7.5 7.5 0 1 0 0 15A7.5 7.5 0 0 0 8 .5zm0 1.6a5.9 5.9 0 0 1 5.6 4H10l-1.2-1.6L6.5 5 5 3.3 3.8 4A5.9 5.9 0 0 1 8 2.1zM2.3 7.5l2.4 1.6.6 2.4 1.4 1.2v1.1A5.9 5.9 0 0 1 2.3 7.5zm6.3 6.3v-1.7l2.3-2.4 1.9.2a5.9 5.9 0 0 1-4.2 3.9z"/></svg>
        www.dulomhome.com
      </li>
    </ul>
  </div>

  <svg class="credential-band" viewBox="0 0 746 56" aria-hidden="true">
    <polygon points="0,36 358,36 376,0 735,0 735,56 0,56" fill="var(--card-dark)"/>
    <rect x="735" y="0" width="11" height="56" fill="var(--accent-red)"/>
  </svg>
  <p class="credentials">LICENSED | INSURED | BONDED</p>
</section>

<section class="card card-back" aria-label="Business card back">
  <div class="wordmark">
    <div class="wordmark-row">
      <span class="wordmark-square"></span>
      <span class="wordmark-name">DULOM</span>
    </div>
    <span class="wordmark-tagline">HOME REMODELING</span>
  </div>

  <div class="social-row" aria-label="Social media links">
    <span class="social-rule"></span>
    <span class="social-dot"></span>
    <span class="social-dot"></span>
    <span class="social-dot"></span>
    <span class="social-rule"></span>
  </div>
</section>

</body>
</html>
```